Hop Bright Meadow Business Website Branding

Looking for a wordpress template design with CSS and HTML encoding. Current website can be seen at hopbrightmeadow.example.

WE ARE CURRENTLY IN PROCESS GETTING A LOGO DESIGN... I HAVE INCLUDED THE TOP POTENTIAL DESIGNS FOR REFERENCE TO HELP UNDERSTAND WHAT STYLE WE ARE LOOKING FOR...
NOTE: THE “PEBBLE CREW” LOGO WAS A PREVIOUS COMPANY WE OWNED SO YOU CAN GE A FEEL FOR THE TYPE OF DESIGNS WE HAVE USED IN THE PAST.

My blog will focus on making a connection with wild Florida, it’s wildlife, plants and animals... with an eye toward Florida conservation, nature adventure trips, and education... Content, photos and other merchandise will also be offered for sale.
I’m looking for a site design that incorporates Florida nature and wildlife/plants, with a fun “Old Florida” retro-adventure feel.
When they see this site it should speak to the import of natural Florida and the critical nature of the ecosystem here... while being instantly recognizable and iconic... IE: when I think of florida I think of water, plants, warmth, sunsets etc...

https://join.chatroomhub.example/t/lumexstudio-kzt4821/shared_invite/zt-pqwrt83m-hRnLvXaKoPzsYcB1Uq7JdM

Target Market(s)

Nature, Education, Conservation, Photography

Industry/Entity Type

Photographer

Coding

Coded - Design and coding required

Requirements
Must have
• Need to have site wide template design which generally includes a landing page and a general page template for other pages... Must include html and css encoding...
Should not have
• Any animals included in the site should be Florida native... IE: no African animals etc... This will require some research to ensure that if animals are included that they are part of the Florida ecosystem.

```html
<!DOCTYPE html>
<html lang="en">
<head>
<meta charset="utf-8">
<title>Hop Bright Meadow – Exploring Florida's Natural Wonders</title>
<link href="https://fonts.googleapis.com/css2?family=Roboto:wght@400;500;700;900&family=Roboto+Slab:wght@400;500&display=swap" rel="stylesheet">
<style>
:root{
  --green:#3f6a1d;
  --green-dark:#2f5313;
  --green-band:#4d7a2a;
  --green-soft:#8fa864;
  --cream:#f8efe2;
  --parchment:#efe1c3;
  --ink:#1f1f1a;
  --text:#4a4438;
  --footer:#1c1c17;
  --white:#ffffff;
}
*{box-sizing:border-box;margin:0;padding:0}
html,body{width:1200px;height:4019px;overflow:hidden}
body{position:relative;background:var(--cream);font-family:"Roboto Slab",serif;color:var(--text)}
.abs{position:absolute}
.heading{font-family:"Roboto",sans-serif;font-weight:900;color:var(--ink);text-transform:uppercase;letter-spacing:.3px}
.rule{position:absolute;height:3px;background:var(--green)}
.btn{position:absolute;display:flex;align-items:center;justify-content:center;background:var(--green-dark);color:var(--white);font-family:"Roboto",sans-serif;font-weight:700;font-size:14px;border-radius:22px;text-transform:uppercase}

/* hero */
.hero{position:absolute;left:0;top:0;width:1200px;height:760px;
  background:linear-gradient(180deg,#1f3550 0%,#3e5670 14%,#a36a3a 32%,#e59a38 44%,#f0b24a 50%,#8a4d22 58%,#5b3a22 72%,#3a2a1e 100%)}
.hero-palms{position:absolute;right:0;top:0;width:420px;height:700px;background:linear-gradient(200deg,rgba(10,20,10,.75),rgba(10,20,10,0) 70%)}
.logo{position:absolute;left:143px;top:58px;display:flex;align-items:center;gap:10px;font-family:"Roboto",sans-serif;font-weight:700;font-size:27px;color:var(--white)}
.logo .mark{width:18px;height:18px;border-radius:50%;background:var(--white)}
.nav{position:absolute;top:83px;font-family:"Roboto",sans-serif;font-weight:700;font-size:14px;color:var(--white);transform:translateX(-50%);white-space:nowrap}
.hero-title{position:absolute;top:262px;left:0;width:1200px;text-align:center;font-family:"Roboto",sans-serif;font-weight:900;font-size:78px;color:var(--white)}
.hero-sub{position:absolute;top:362px;left:0;width:1200px;text-align:center;font-family:"Roboto",sans-serif;font-size:33px;color:var(--white)}
.dots{position:absolute;top:640px;left:566px;display:flex;gap:4px}
.dots span{width:13px;height:13px;border:1.5px solid var(--white);border-radius:50%}

/* about */
.about{position:absolute;left:0;top:735px;width:1200px;height:640px;background:var(--parchment)}
.about p{position:absolute;left:601px;top:955px;width:495px;font-size:15px;line-height:24px}

/* welcome */
.welcome-sub{position:absolute;top:1596px;left:0;width:1200px;text-align:center;font-size:21px;color:var(--text)}
.welcome-text{position:absolute;top:1636px;left:228px;width:744px;text-align:center;font-size:13.5px;line-height:26px}

/* blog */
.blog{position:absolute;left:0;top:1903px;width:1200px;height:820px;background:linear-gradient(180deg,#4e7b2b,#5a8632 50%,#47722a)}
.card{position:absolute;width:292px;height:476px;background:var(--cream);box-shadow:0 2px 8px rgba(0,0,0,.2)}
.card .photo{position:absolute;left:18px;top:25px;width:256px;height:203px;border-radius:14px}
.card .date{position:absolute;left:22px;top:253px;font-family:"Roboto",sans-serif;font-weight:700;font-size:13px;color:var(--green);display:flex;align-items:center;gap:8px}
.card h3{position:absolute;left:22px;top:276px;width:250px;font-family:"Roboto",sans-serif;font-weight:700;font-size:15px;line-height:21px;color:var(--ink)}
.card p{position:absolute;left:22px;top:331px;width:250px;font-family:"Roboto",sans-serif;font-size:13.5px;line-height:20px;color:var(--text)}
.card .read{position:absolute;left:18px;top:411px;width:123px;height:32px;border:1.5px solid var(--green);border-radius:16px;display:flex;align-items:center;justify-content:center;font-size:12.5px;color:var(--green);text-transform:uppercase}

/* gallery */
.tile{position:absolute}

/* footer */
.footer{position:absolute;left:0;top:3448px;width:1200px;height:571px;background:var(--footer);color:#e8e4da}
.f-h{position:absolute;font-family:"Roboto",sans-serif;font-weight:700;font-size:23px;color:var(--white)}
.f-t{position:absolute;font-size:15px;line-height:19px;color:#e8e4da}
.social{position:absolute;width:27px;height:27px;border:1.5px solid #e8e4da;border-radius:50%}
</style>
</head>
<body>

<!-- Hero -->
<section class="hero" role="img" aria-label="Photograph of a Florida beach at sunset with palm trees and rocks">
  <div class="hero-palms"></div>
</section>
<div class="logo"><span>Hop Bright Meadow</span><span class="mark"></span></div>
<span class="nav" style="left:485px">HOME</span>
<span class="nav" style="left:573px">ABOUT US</span>
<span class="nav" style="left:674px">SERVICES</span>
<span class="nav" style="left:811px">NATURE ADVENTURE</span>
<span class="nav" style="left:935px">BLOG</span>
<span class="nav" style="left:1021px">CONTACT</span>
<h1 class="hero-title">Hop Bright Meadow!</h1>
<p class="hero-sub">Exploring Florida's Natural Wonders</p>
<div class="btn" style="left:466px;top:429px;width:269px;height:44px">Book an appointment</div>
<div class="dots"><span></span><span></span><span></span><span></span></div>

<!-- About -->
<section class="about"></section>
<svg class="abs" style="left:0;top:650px" width="1200" height="140" viewBox="0 0 1200 140">
  <path d="M0 90 C250 40 450 150 700 130 C900 115 1080 60 1200 10 L1200 140 L0 140Z" fill="var(--parchment)"/>
  <path d="M0 85 C250 40 450 130 700 118 C900 108 1080 55 1200 5 C1080 70 900 130 700 142 C450 155 250 60 0 95Z" fill="var(--green)"/>
</svg>
<svg class="abs" style="left:0;top:1330px" width="1200" height="70" viewBox="0 0 1200 70">
  <path d="M0 30 L40 18 L70 34 L110 22 L150 40 L200 26 L240 44 L300 30 L360 46 L420 28 L480 42 L540 30 L600 46 L660 32 L720 44 L780 28 L840 42 L900 26 L960 40 L1020 24 L1080 38 L1140 22 L1200 34 L1200 70 L0 70Z" fill="var(--cream)"/>
</svg>
<div class="abs" style="left:81px;top:916px;width:212px;height:212px;border-radius:50%;background:var(--green-soft)"></div>
<div class="abs" style="left:140px;top:1100px;width:188px;height:188px;border-radius:50%;background:var(--green-soft)"></div>
<div class="abs" role="img" aria-label="Portrait photograph of the naturalist at the beach" style="left:169px;top:899px;width:376px;height:376px;border-radius:50%;border:3px solid var(--white);background:linear-gradient(160deg,#c98a5a,#7aa0b8 55%,#3f9fb0)"></div>
<h2 class="heading abs" style="left:601px;top:858px;font-size:38px">About Marisol Penhallow</h2>
<div class="rule" style="left:601px;top:930px;width:86px"></div>
<p class="abs" style="left:601px;top:955px;width:495px;font-size:15px;line-height:24px">Hello nature lovers! I’m Marisol Penhallow, a wildlife educator, Florida Master Naturalist, nature writer and photographer, busy mama of three kiddos, a playful Havanese puppy, two very chubby guinea pigs, and a giant tree frog. I have a passion for all things nature and I adore living in Southwest Florida. I will always be a California girl, but from the moment I set foot in Florida, its wild beauty stole my heart. For the past 23 years, I have been fortunate to have some very unique and special experiences caring for many different species of animals and educating the public about wildlife and the environment. My hope</p>
<div class="btn" style="left:601px;top:1222px;width:168px;height:41px">Learn more</div>

<!-- Welcome -->
<h2 class="heading abs" style="left:0;top:1490px;width:1200px;text-align:center;font-size:39px">Welcome to Hop Bright Meadow!</h2>
<div class="rule" style="left:571px;top:1567px;width:58px"></div>
<p class="welcome-sub">Exploring Florida’s Natural Wonders</p>
<p class="welcome-text">Come explore wild places and stunning scenery with me as I discover new and exciting eco-adventures and learn about the rare and unique wildlife and environments that make Florida so precious and extraordinary. I hope you can vicariously enjoy the wild and untamed beauty of Florida through my eyes, and learn some amazing things about nature on our explorations</p>
<div class="btn" style="left:516px;top:1775px;width:168px;height:42px">Learn more</div>

<!-- Blog -->
<section class="blog" role="img" aria-label="Background photograph of a misty green forest"></section>
<svg class="abs" style="left:0;top:1890px" width="1200" height="50" viewBox="0 0 1200 50">
  <path d="M0 0 L1200 0 L1200 22 L1150 34 L1100 18 L1040 30 L980 14 L920 32 L860 20 L800 36 L740 16 L680 30 L620 12 L560 32 L500 18 L440 34 L380 16 L320 30 L260 14 L200 32 L140 18 L80 30 L30 16 L0 26Z" fill="var(--cream)"/>
</svg>
<svg class="abs" style="left:0;top:2690px" width="1200" height="50" viewBox="0 0 1200 50">
  <path d="M0 24 L50 36 L110 18 L170 34 L230 14 L290 30 L350 18 L410 36 L470 16 L530 32 L590 20 L650 38 L710 16 L770 32 L830 18 L890 36 L950 14 L1010 30 L1070 20 L1130 34 L1200 20 L1200 50 L0 50Z" fill="var(--cream)"/>
</svg>
<h2 class="heading abs" style="left:0;top:2001px;width:1200px;text-align:center;font-size:39px;color:var(--white)">Latest Blog</h2>
<div class="rule" style="left:571px;top:2058px;width:58px;background:var(--white)"></div>

<article class="card" style="left:125px;top:2087px">
  <div class="photo" role="img" aria-label="Photograph of a sunset over the sea" style="background:linear-gradient(180deg,#4a6b85,#c9683a 60%,#3a3a40)"></div>
  <div class="date"><svg width="12" height="12" viewBox="0 0 12 12"><rect x="1" y="2" width="10" height="9" fill="none" stroke="currentColor" stroke-width="1.5"/><line x1="1" y1="5" x2="11" y2="5" stroke="currentColor" stroke-width="1.5"/></svg>OCT 17, 2020</div>
  <h3>FLORIDA MASTER NATURALIST UPLANDS NATURE JOURNAL</h3>
  <p>Sed ut perspiciatis unde omnis iste natus sit voluptatem accusantium doloremque laudantium</p>
  <div class="read">Read more</div>
</article>
<article class="card" style="left:452px;top:2118px">
  <div class="photo" role="img" aria-label="Photograph of an underwater coral reef" style="background:linear-gradient(180deg,#1a7fc8,#0e4f95 55%,#5a6a50)"></div>
  <div class="date"><svg width="12" height="12" viewBox="0 0 12 12"><rect x="1" y="2" width="10" height="9" fill="none" stroke="currentColor" stroke-width="1.5"/><line x1="1" y1="5" x2="11" y2="5" stroke="currentColor" stroke-width="1.5"/></svg>OCT 17, 2020</div>
  <h3>FLORIDA MASTER NATURALIST UPLANDS NATURE JOURNAL</h3>
  <p>Sed ut perspiciatis unde omnis iste natus sit voluptatem accusantium doloremque laudantium</p>
  <div class="read">Read more</div>
</article>
<article class="card" style="left:782px;top:2087px">
  <div class="photo" role="img" aria-label="Photograph of purple wildflowers" style="background:linear-gradient(160deg,#4a6a2e,#a55cb8 50%,#3e5a26)"></div>
  <div class="date"><svg width="12" height="12" viewBox="0 0 12 12"><rect x="1" y="2" width="10" height="9" fill="none" stroke="currentColor" stroke-width="1.5"/><line x1="1" y1="5" x2="11" y2="5" stroke="currentColor" stroke-width="1.5"/></svg>OCT 17, 2020</div>
  <h3>FLORIDA MASTER NATURALIST UPLANDS NATURE JOURNAL</h3>
  <p>Sed ut perspiciatis unde omnis iste natus sit voluptatem accusantium doloremque laudantium</p>
  <div class="read">Read more</div>
</article>

<!-- Gallery -->
<h2 class="heading abs" style="left:0;top:2791px;width:1200px;text-align:center;font-size:39px">Our Gallery</h2>
<div class="rule" style="left:557px;top:2849px;width:86px"></div>
<div class="tile" role="img" aria-label="Photograph of palms under a blue sky" style="left:143px;top:2894px;width:234px;height:221px;background:linear-gradient(180deg,#2f6fc0,#9ab8d8 45%,#3c5a2a)"></div>
<div class="tile" role="img" aria-label="Photograph of a white egret" style="left:381px;top:2894px;width:241px;height:221px;background:linear-gradient(160deg,#7a7048,#d8d2c0 50%,#5e5a38)"></div>
<div class="tile" role="img" aria-label="Photograph of butterflies on orange flowers" style="left:626px;top:2894px;width:427px;height:449px;background:linear-gradient(150deg,#3d5a22,#f0a030 45%,#e8862a 65%,#4a5e22)"></div>
<div class="tile" role="img" aria-label="Photograph of a snake among leaves" style="left:143px;top:3118px;width:305px;height:225px;background:linear-gradient(160deg,#3e7a2a,#b0a468 50%,#2e4e22)"></div>
<div class="tile" role="img" aria-label="Photograph of a city lake with swans" style="left:451px;top:3118px;width:171px;height:225px;background:linear-gradient(180deg,#b8c4cc,#8c8a80 55%,#6a6a60)"></div>

<!-- Footer -->
<footer class="footer"></footer>
<svg class="abs" style="left:0;top:3420px" width="1200" height="60" viewBox="0 0 1200 60">
  <path d="M0 40 L40 26 L90 44 L140 20 L200 40 L260 22 L320 44 L380 24 L440 42 L500 18 L560 40 L620 24 L680 44 L740 20 L800 42 L860 24 L920 44 L980 22 L1040 40 L1100 20 L1160 38 L1200 24 L1200 60 L0 60Z" fill="var(--footer)"/>
</svg>
<div class="abs" style="left:123px;top:3598px;display:flex;align-items:center;gap:10px;font-family:'Roboto',sans-serif;font-weight:700;font-size:24px;color:var(--white)"><span>Hop Bright Meadow</span></div>
<p class="f-t" style="left:123px;top:3690px;width:240px">Sed ut perspiciatis unde omnis iste natus error sit voluptatem accuium doloremque launtium, totam rem aperiam, eaque</p>
<span class="social" style="left:122px;top:3775px"></span>
<span class="social" style="left:156px;top:3775px"></span>
<span class="social" style="left:190px;top:3775px"></span>
<span class="social" style="left:225px;top:3775px"></span>

<h4 class="f-h" style="left:401px;top:3590px">Sign up for newsletter</h4>
<p class="f-t" style="left:401px;top:3652px;width:290px">excepteur sint occaecat cupidatat non proident, sunt in culpa qui officia</p>
<div class="abs" style="left:401px;top:3699px;width:273px;height:38px;background:var(--white);border-radius:3px;font-family:'Roboto',sans-serif;font-size:12px;color:#555;padding:12px 14px">Enter email</div>
<div class="abs" style="left:401px;top:3754px;width:139px;height:35px;background:var(--green);display:flex;align-items:center;justify-content:center;font-family:'Roboto',sans-serif;font-weight:700;font-size:14px;color:var(--white)">SUBSCRIBE</div>

<h4 class="f-h" style="left:711px;top:3592px">Contact us</h4>
<svg class="abs" style="left:714px;top:3652px" width="16" height="22" viewBox="0 0 16 22"><path d="M8 0C3.6 0 0 3.5 0 7.8 0 13.5 8 22 8 22s8-8.5 8-14.2C16 3.5 12.4 0 8 0zm0 11a3 3 0 110-6 3 3 0 010 6z" fill="#e8e4da"/></svg>
<p class="f-t" style="left:749px;top:3652px;width:190px">Hop Bright Meadow!<br>405 quis risus ac ante feugiat</p>
<svg class="abs" style="left:713px;top:3735px" width="16" height="16" viewBox="0 0 16 16"><path d="M3.5 0.5l3 3-2 2.2c1 2.2 2.6 3.8 4.8 4.8l2.2-2 3 3-2 2.5C7 13.5 2.5 9 1 2.5z" fill="#e8e4da"/></svg>
<p class="f-t" style="left:749px;top:3732px;width:220px">Phone: (555) 0142-7731<br>Fax:(555) 0198-2264</p>
<svg class="abs" style="left:714px;top:3790px" width="17" height="12" viewBox="0 0 17 12"><rect width="17" height="12" fill="#e8e4da"/><path d="M0 0l8.5 7L17 0" fill="none" stroke="#1c1c17" stroke-width="1.5"/></svg>
<p class="f-t" style="left:749px;top:3782px;width:240px">Email:<br>info@hopbrightmeadow.example</p>

<h4 class="f-h" style="left:981px;top:3589px">Quick links</h4>
<p class="f-t" style="left:986px;top:3639px">Home</p>
<p class="f-t" style="left:986px;top:3666px">Services</p>
<p class="f-t" style="left:986px;top:3693px">About Us</p>
<p class="f-t" style="left:986px;top:3721px">Contact Us</p>

<div class="abs" style="left:0;top:3908px;width:1200px;height:1px;background:#33332b"></div>
<p class="abs" style="left:0;top:3960px;width:1200px;text-align:center;font-size:14.5px;color:#e8e4da">Hop Bright Meadow! © 2020 All Rights Reserved | Privacy Policy | Terms and Conditions</p>

</body>
</html>
```